Business Card for Multi-Brand Sportswear Company

We are looking for a business card which represents our company and the multiple brands within it.

The company: Fen Athletics (LTD)
The brands: Fen, TavaPuni, ElmStretch, Grit and Rain

Employees using these cards would be representing Fen Athletics, rather than any of the individual brands. You will see a current design within the uploaded files, to give some inspiration. The actual text of the brands is not necessary, but the logos should be on there is some format.

Our creative minds on this are stretched, so we are looking for someone to make this their own, and show us what a good business card should look like.

We may like to get these printed with spot gloss, so keep that in mind with your designs.

www.fenathletics.co.uk

Industry/Entity Type

Business

Contact Information for Business Card

Leo Pemberton-Hale
Operations Manager
(+44) 1632 960 418
Leo@fenathletics.co.uk
www.fenathletics.co.uk

Font styles to use
Sans Serif
Other font styles liked:
• Eurostile

Colors
ffffff

Requirements
Nice to have
• Dark (black) background

```html
<!DOCTYPE html>
<html lang="en">
<head>
<meta charset="utf-8">
<title>Fen Athletics Business Card</title>
<link href="https://fonts.googleapis.com/css2?family=Michroma&family=Open+Sans:wght@400;600&display=swap" rel="stylesheet">
<style>
  :root {
    --backdrop: #2a2421;
    --card: #262626;
    --card-hi: #333333;
    --ink: #e6e6e6;
    --ink-soft: #bdbdbd;
    --rule: #6d6d6d;
    --red: #e3232b;
    --white: #ffffff;
    --brand-a: #6a5a82;
    --brand-b: #d9d9d9;
    --brand-c: #e9e0df;
    --brand-d: #d4d4d4;
  }
  * { box-sizing: border-box; margin: 0; padding: 0; }
  html, body { width: 1200px; height: 716px; overflow: hidden; background: var(--backdrop); }
  .canvas {
    position: relative; width: 1200px; height: 716px;
    display: flex; align-items: center; justify-content: center; gap: 40px;
  }
  .card {
    position: relative; width: 540px; height: 350px; overflow: hidden;
    background: radial-gradient(ellipse at 45% 30%, var(--card-hi), var(--card) 70%);
    box-shadow: 0 18px 40px rgba(0,0,0,.45);
  }
  .stripe { position: absolute; left: 0; right: 0; bottom: 0; height: 14px; display: flex; }
  .stripe .red { width: 46%; background: var(--red); }
  .stripe .white { flex: 1; background: var(--white); }

  .wordmark {
    font-family: "Michroma", sans-serif; color: var(--ink);
    letter-spacing: 1px; white-space: nowrap;
  }
  .tagline {
    font-family: "Open Sans", sans-serif; font-size: 6px; letter-spacing: 1.5px;
    color: var(--ink-soft); text-transform: uppercase;
  }
  .rule { height: 2px; background: var(--rule); }
  .brands { display: flex; gap: 16px; }
  .brand-badge { width: 44px; height: 30px; border-radius: 3px; }
  .brand-badge.tavapuni { background: var(--brand-a); border: 2px solid #b9aed0; }
  .brand-badge.elmstretch { background: var(--brand-b); }
  .brand-badge.grit-rain { background: var(--brand-c); }
  .brand-badge.fen { background: var(--brand-d); }

  /* front */
  .front .logo-block { position: absolute; left: 190px; top: 80px; width: 240px; }
  .front .wordmark { font-size: 24px; }
  .front .tagline { text-align: right; margin-top: 2px; }
  .front .rule { margin-top: 6px; }
  .front .brands { position: absolute; left: 120px; top: 150px; gap: 30px; }

  /* back */
  .back .logo-block { position: absolute; left: 48px; top: 46px; width: 190px; }
  .back .wordmark { font-size: 17px; }
  .back .tagline { text-align: right; margin-top: 2px; font-size: 5px; }
  .back .rule { margin-top: 4px; }
  .back .brands { position: absolute; left: 30px; top: 42px; gap: 10px; }
  .back .brands .brand-badge { width: 28px; height: 20px; }
  .company {
    position: absolute; left: 30px; top: 110px;
    font-family: "Michroma", sans-serif; font-size: 13px; letter-spacing: 3px;
    color: var(--ink); text-transform: uppercase;
  }
  .person { position: absolute; left: 30px; top: 140px; font-family: "Open Sans", sans-serif; color: var(--ink); }
  .person .name { font-size: 17px; font-weight: 600; }
  .person .role { font-size: 11px; color: var(--ink-soft); margin-left: 50px; }
  .contact {
    position: absolute; right: 30px; bottom: 40px; text-align: right;
    font-family: "Open Sans", sans-serif; font-size: 13px; line-height: 1.45; color: var(--ink);
  }
  .contact .web { letter-spacing: 2px; margin-bottom: 18px; }
  .contact .address { margin-bottom: 14px; }
</style>
</head>
<body>
<main class="canvas">
  <section class="card front" aria-label="Card front">
    <div class="logo-block">
      <div class="wordmark">Fen Athletics</div>
      <div class="rule"></div>
      <div class="tagline">Performance Wear</div>
    </div>
    <div class="brands" aria-label="Brand family">
      <div class="brand-badge tavapuni" title="TavaPuni"></div>
      <div class="brand-badge elmstretch" title="ElmStretch"></div>
      <div class="brand-badge grit-rain" title="Grit and Rain"></div>
      <div class="brand-badge fen" title="Fen"></div>
    </div>
    <div class="stripe"><span class="red"></span><span class="white"></span></div>
  </section>

  <section class="card back" aria-label="Card back">
    <div class="logo-block">
      <div class="wordmark">Fen Athletics</div>
      <div class="rule"></div>
      <div class="tagline">Performance Wear</div>
    </div>
    <div class="brands" style="top:78px" aria-label="Brand family">
      <div class="brand-badge tavapuni" title="TavaPuni"></div>
      <div class="brand-badge elmstretch" title="ElmStretch"></div>
      <div class="brand-badge grit-rain" title="Grit and Rain"></div>
      <div class="brand-badge fen" title="Fen"></div>
    </div>
    <div class="company">Fen Athletics (LTD)</div>
    <div class="person">
      <div class="name">Leo Pemberton-Hale</div>
      <div class="role">Operations Manager</div>
    </div>
    <div class="contact">
      <div class="web">www.fenathletics.co.uk</div>
      <div class="address">Low Field Lane, Ashby,<br>Ripon, HG9 4QT</div>
      <div class="phone">(+44) 1632 960 418</div>
      <div class="email">Leo@fenathletics.co.uk</div>
    </div>
    <div class="stripe"><span class="red"></span><span class="white"></span></div>
  </section>
</main>
</body>
</html>
```